Business Card Design for Marketing Firm

Looking for business card design for higher end marketing firm. Clean but impressionable/trendy. We are a marketing firm that represents manufacturers in the foodservice equipment and supply industry. Our customers are end users such has hotels, restaurants, country clubs, convention centers and casinos as well as distributors of restaurants supplies and equipment, and manufacturers of foodservice equipment and supplies.
Target Market(s)
Hotels, Restaurants, Supply & Equipment Distributors, Foodservice Manufacturers
Industry/Entity Type
Foodservice/Hospitality
Contact Information for Business Card
Name, Title, Contact Number, Email, Website, Social Media, Address
Requirements
Must have
- Clean & Simple but Serious and Impressionable

```html
<!DOCTYPE html>
<html lang="en">
<head>
<meta charset="utf-8">
<title>Meridian Hospitality Reps — Business Card</title>
<link href="https://fonts.googleapis.com/css2?family=Tinos:wght@700&family=Arimo:wght@400;700&display=swap" rel="stylesheet">
<style>
  :root {
    --navy: #0c0b7c;
    --navy-deep: #08085e;
    --paper: #f4f5f7;
    --ink: #222222;
    --ink-grey: #5d5f66;
    --rule-blue: #4f6fa0;
    --backdrop: #e7e8ec;
    --white: #ffffff;
  }
  * { box-sizing: border-box; margin: 0; padding: 0; }
  html, body { width: 1200px; height: 779px; overflow: hidden; background: var(--backdrop); }
  .canvas { position: relative; width: 1200px; height: 779px; }

  .card { position: absolute; border-radius: 22px; box-shadow: 0 10px 28px rgba(0,0,0,.18); }

  /* Front */
  .card-front {
    left: 95px; top: 246px; width: 510px; height: 292px;
    background: var(--navy);
    display: flex; align-items: center; justify-content: center;
  }
  .brand {
    display: flex; align-items: center; gap: 12px;
    font-family: "Tinos", serif; font-weight: 700; letter-spacing: 1px;
  }
  .brand-dot { width: 14px; height: 14px; border-radius: 50%; flex: none; }
  .brand-front { color: var(--white); font-size: 28px; }
  .brand-front .brand-dot { background: var(--white); }

  /* Back */
  .card-back {
    left: 700px; top: 127px; width: 300px; height: 525px;
    background: var(--paper);
    border-right: 3px solid var(--navy);
    border-bottom: 3px solid var(--navy);
    padding: 46px 36px 0 40px;
  }
  .social { position: absolute; top: 26px; right: 26px; display: flex; gap: 6px; }
  .social span { width: 15px; height: 15px; border-radius: 50%; background: var(--navy-deep); }

  .brand-back { color: var(--navy); font-size: 24px; margin-top: 24px; }
  .brand-back .brand-dot { background: var(--navy); width: 12px; height: 12px; }

  .person { margin-top: 46px; }
  .person-name { font-family: "Tinos", serif; font-weight: 700; font-size: 24px; color: var(--navy); letter-spacing: .5px; }
  .person-title { font-family: "Arimo", sans-serif; font-size: 14px; color: var(--ink-grey); margin-top: 2px; }

  .divider { width: 32px; height: 1.5px; background: var(--rule-blue); margin: 26px 0; }

  .address { font-family: "Arimo", sans-serif; font-style: normal; font-size: 15px; color: var(--ink); line-height: 1.45; }
  .contacts { font-family: "Arimo", sans-serif; font-size: 15px; color: var(--ink); line-height: 1.5; list-style: none; }
  .contacts b { color: var(--navy); font-weight: 700; display: inline-block; width: 28px; }
</style>
</head>
<body>
<main class="canvas">
  <section class="card card-front" aria-label="Card front">
    <div class="brand brand-front">
      <span class="brand-dot"></span>
      <span class="brand-name">MERIDIAN HOSPITALITY REPS</span>
    </div>
  </section>

  <section class="card card-back" aria-label="Card back">
    <div class="social" aria-label="Social media"><span></span><span></span><span></span></div>
    <div class="brand brand-back">
      <span class="brand-dot"></span>
      <span class="brand-name">MERIDIAN</span>
    </div>

    <div class="person">
      <div class="person-name">DANIEL CARTER</div>
      <div class="person-title">President</div>
    </div>

    <div class="divider"></div>
    <address class="address">
      2716 Harbor View Lane<br>Glen Oaks, NY 11004
    </address>

    <div class="divider"></div>
    <ul class="contacts">
      <li><b>P :</b>(555) 8120-4471</li>
      <li><b>E :</b>name@MERIDIAN.com</li>
      <li><b>W :</b>www.MERIDIAN.com</li>
    </ul>
  </section>
</main>
</body>
</html>
```